Website setup with Brightline (childtheme is velmora theme)

hey there, my name is tobias and i would need a website. Tundrix Framework, I use the velmora theme. I would like to say goodbye to the eye-catching website with a nice menu. I like to send you some example from websites I like. Https://harborquillnotes.com/about/ https://harborquillnotes.com The main tabs on the top should be "About", "Blog", "Video", "Resources" on the right / blog /

Number of Pages Required

1 page

Colors
0493ce
fbee3d
faa54b

```html
<!DOCTYPE html>
<html lang="en">
<head>
<meta charset="utf-8">
<title>Tobias Life</title>
<link href="https://fonts.googleapis.com/css2?family=Lato:wght@300;400;700;900&display=swap" rel="stylesheet">
<style>
:root{
  --blue:#1e8cf0;
  --blue-dark:#1577d4;
  --ink:#222428;
  --text:#555a60;
  --muted:#8a8f95;
  --light:#f4f4f4;
  --white:#ffffff;
  --dark:#1f2124;
  --footer:#2a2c2f;
  --hero-a:#121416;
  --hero-b:#3a3c40;
}
*{box-sizing:border-box;margin:0;padding:0}
html,body{width:1200px;height:5172px;overflow:hidden}
body{font-family:"Lato",Arial,sans-serif;color:var(--text);background:var(--white);position:relative}
section,header,footer{position:absolute;left:0;width:1200px}
.btn{display:inline-block;background:var(--blue);color:var(--white);font-size:15px;font-weight:700;padding:11px 26px;border-radius:3px}
.section-title{text-align:center;color:var(--blue);font-size:30px;font-weight:700}
.photo{position:absolute}
p{font-size:14px;line-height:1.6}

/* Hero */
.hero{top:0;height:700px;background:linear-gradient(90deg,var(--hero-a) 0%,var(--hero-b) 50%,var(--hero-a) 100%)}
.hero-photo{left:330px;top:0;width:540px;height:700px;background:radial-gradient(ellipse at 50% 40%,#6b5a4e 0%,#3a3230 45%,transparent 75%)}
.topbar{position:absolute;top:0;left:0;width:1200px;height:80px;display:flex;align-items:center;justify-content:space-between;padding:0 52px}
.brand{color:var(--white);font-size:38px;font-weight:700}
.nav{display:flex;gap:6px}
.nav a{color:var(--white);font-size:15px;text-decoration:none;padding:6px 12px}
.nav a.active{background:var(--blue);border-radius:2px}
.hero-copy{position:absolute;left:158px;top:236px;color:var(--white)}
.hero-copy .kicker{font-size:34px;font-weight:400}
.hero-copy h1{font-size:64px;font-weight:700;line-height:1.1;margin-bottom:34px}
.arrow{position:absolute;top:330px;width:28px;height:28px;background:rgba(255,255,255,.15)}

/* Signup */
.signup{position:absolute;left:160px;top:638px;width:880px;height:282px;background:var(--blue);text-align:center;color:var(--white);z-index:2}
.signup h2{font-size:24px;font-weight:900;margin:48px 0 30px}
.signup form{display:flex;justify-content:center;gap:14px}
.field{width:236px;height:42px;background:var(--white);color:var(--muted);font-size:13px;text-align:left;padding:13px 16px;border-radius:2px}
.submit{width:200px;height:42px;background:var(--dark);color:var(--white);font-size:13px;font-weight:700;padding:13px;border-radius:2px}
.signup small{display:block;margin-top:32px;font-size:12px;opacity:.85}

/* About */
.about{top:700px;height:860px;background:var(--light)}
.about-photo{left:560px;top:280px;width:640px;height:580px;background:linear-gradient(90deg,var(--light) 0%,#b9b9b9 30%,#5d5d5d 65%,#8d8d8d 100%)}
.about-copy{position:absolute;left:130px;top:310px;width:360px}
.about-copy h2{color:var(--blue);font-size:40px;font-weight:700;margin-bottom:12px}
.about-copy .rule{width:400px;height:1px;background:#d5d5d5;margin-bottom:22px}
.about-copy p{margin-bottom:40px;font-size:13px}

/* Program */
.program{top:1560px;height:790px;background:var(--white)}
.program .section-title{margin-top:110px}
.cards{position:absolute;top:220px;left:130px;display:flex;gap:20px}
.card{width:300px;text-align:center}
.card .photo{position:static;height:290px}
.card h3{color:var(--ink);font-size:20px;font-weight:700;margin:30px 0 12px}
.card p{font-size:12px;width:240px;margin:0 auto 18px}
.card .btn{font-size:12px;padding:9px 22px}

/* Testimonial */
.quote{top:2350px;height:440px;background:linear-gradient(180deg,#1b2233 0%,#2f3850 55%,#161b26 100%)}
.quote-body{position:absolute;left:290px;top:70px;width:620px;color:var(--white);text-align:center}
.quote-body p{font-size:16px;line-height:1.45}
.quote-mark{position:absolute;color:var(--white);font-size:60px;font-weight:900;line-height:1}
.avatar{width:42px;height:42px;border-radius:50%;background:#b58f79;margin:34px auto 6px}
.quote-body .name{font-size:12px}
.chev{position:absolute;top:196px}

/* Difference */
.difference{top:2790px;height:650px;background:var(--light)}
.difference .section-title{margin-top:80px}
.features{position:absolute;top:200px;left:160px;display:grid;grid-template-columns:440px 440px;column-gap:60px;row-gap:60px}
.feature{display:flex;gap:30px}
.feature svg{flex:none}
.feature h4{color:var(--ink);font-size:17px;font-weight:700;margin:8px 0 12px}
.feature p{font-size:12px}
.vline{position:absolute;left:600px;top:190px;width:1px;height:380px;background:#dcdcdc}

/* Resources */
.resources{top:3440px;height:740px;background:var(--white)}
.resources .section-title{margin-top:90px}
.tiles{position:absolute;top:184px;left:150px;display:grid;grid-template-columns:repeat(3,280px);gap:30px}
.tile{position:relative;height:200px}
.tile span{position:absolute;left:16px;bottom:16px;color:var(--white);font-size:12px;font-weight:700}

/* Blog */
.blog{top:4180px;height:440px;background:var(--light)}
.blog .section-title{margin-top:70px}
.posts{position:absolute;top:140px;left:160px;display:flex;gap:40px}
.post{position:relative;width:420px;height:240px;background:var(--white);box-shadow:0 2px 8px rgba(0,0,0,.08)}
.post h3{color:var(--ink);font-size:18px;font-weight:700;line-height:1.3;margin-bottom:12px}
.post p{font-size:11px;margin-bottom:14px}
.post .btn{font-size:11px;padding:8px 18px}
.post-copy{position:absolute;top:44px;width:260px}
.post .photo{top:0;width:130px;height:240px}
.dots{position:absolute;top:418px;left:570px;display:flex;gap:8px}
.dots i{width:8px;height:8px;border-radius:50%;background:#c8c8c8}
.dots i.on{background:var(--muted)}

/* Footer */
.site-footer{top:4620px;height:552px;background:var(--footer);color:#a0a4a8}
.foot-about{position:absolute;left:120px;top:60px;width:380px}
.foot-about p{font-size:12px;margin-bottom:20px}
.follow{position:absolute;left:660px;top:60px}
.follow h5{color:var(--white);font-size:14px;font-weight:700;margin-bottom:24px}
.socials{display:flex;gap:10px}
.socials i{width:22px;height:22px;border-radius:50%;background:#5b6066}
.foot-nav{position:absolute;top:440px;width:1200px;text-align:center;color:var(--white);font-size:14px;word-spacing:6px}
.foot-rule{position:absolute;top:480px;left:0;width:1200px;height:1px;background:#3b3e42}
.copyright{position:absolute;top:506px;width:1200px;text-align:center;font-size:11px}
</style>
</head>
<body>

<header class="hero">
  <div class="photo hero-photo" role="img" aria-label="Portrait of a man in sunglasses and a dark jacket"></div>
  <div class="topbar">
    <div class="brand">Tobias Life</div>
    <nav class="nav">
      <a class="active">Home</a><a>About</a><a>Blog</a><a>Video</a><a>Resources</a><a>Contact</a>
    </nav>
  </div>
  <div class="arrow" style="left:0"></div>
  <div class="arrow" style="right:0"></div>
  <div class="hero-copy">
    <div class="kicker">WELCOME TO</div>
    <h1>Tobias Life</h1>
    <span class="btn">Read More &#8250;</span>
  </div>
  <div class="signup">
    <h2>LOREM IPSUM IS SIMPLY DUMMY TEXT</h2>
    <form>
      <div class="field">First Name</div>
      <div class="field">Last Name</div>
      <div class="submit">SIGN UP</div>
    </form>
    <small>Join our weekly letter today</small>
  </div>
</header>

<section class="about">
  <div class="photo about-photo" role="img" aria-label="Black and white photo of a man in a tuxedo and sunglasses"></div>
  <div class="about-copy">
    <h2>ABOUT ME</h2>
    <div class="rule"></div>
    <p>But I must explain to you how all this mistaken idea of denouncing pleasure and praising pain was born and I will give you a complete account of the system, and expound the actual teachings of the great explorer of the truth, the master builder of human happiness. No one rejects, dislikes, or avoids pleasure itself, because it is pleasure, but because those who do not know how to pursue pleasure rationally encounter consequences that are extremely painful.</p>
    <span class="btn">Read More &#8250;</span>
  </div>
</section>

<section class="program">
  <h2 class="section-title">What you'll learn from our 3 Step Program</h2>
  <div class="cards">
    <div class="card">
      <div class="photo" style="background:linear-gradient(135deg,#3b4655,#8d9aa8)" role="img" aria-label="Laptop on a desk"></div>
      <h3>Online Marketer</h3>
      <p>But I must explain to you how all this mistaken idea of denouncing pleasure and praising pain was born.</p>
      <span class="btn">Read More</span>
    </div>
    <div class="card">
      <div class="photo" style="background:linear-gradient(135deg,#d9d6d1,#a79b8e)" role="img" aria-label="Man in a suit presenting"></div>
      <h3>Life Coach</h3>
      <p>But I must explain to you how all this mistaken idea of denouncing pleasure and praising pain was born.</p>
      <span class="btn">Read More</span>
    </div>
    <div class="card">
      <div class="photo" style="background:linear-gradient(135deg,#e6e3de,#8c7d6d)" role="img" aria-label="Speaker addressing a seated audience"></div>
      <h3>Business Coach</h3>
      <p>But I must explain to you how all this mistaken idea of denouncing pleasure and praising pain was born.</p>
      <span class="btn">Read More</span>
    </div>
  </div>
</section>

<section class="quote" role="img" aria-label="City skyline at night behind a testimonial">
  <svg class="chev" style="left:40px" width="14" height="24" viewBox="0 0 14 24"><path d="M12 2 2 12l10 10" fill="none" stroke="#fff" stroke-width="3"/></svg>
  <svg class="chev" style="right:40px" width="14" height="24" viewBox="0 0 14 24"><path d="M2 2l10 10-10 10" fill="none" stroke="#fff" stroke-width="3"/></svg>
  <div class="quote-mark" style="left:280px;top:40px">&ldquo;</div>
  <div class="quote-mark" style="left:900px;top:200px">&rdquo;</div>
  <div class="quote-body">
    <p>Lorem ipsum dolor sit amet, consectetur adipiscing elit, sed do eiusmod tempor incididunt ut labore et dolore magna aliqua. Ut enim ad minim veniam, quis nostrud exercitation ullamco laboris nisi ut aliquip ex ea commodo consequat. Duis aute irure dolor in reprehenderit in voluptate velit esse cillum dolore eu fugiat nulla pariatur.</p>
    <div class="avatar" role="img" aria-label="Small client portrait"></div>
    <div class="name">Adrian</div>
  </div>
</section>

<section class="difference">
  <h2 class="section-title">LET'S MAKE A DIFFERENCE</h2>
  <div class="vline"></div>
  <div class="features">
    <div class="feature">
      <svg width="40" height="40" viewBox="0 0 40 40" fill="none" stroke="#1e8cf0" stroke-width="2"><circle cx="20" cy="20" r="17"/><ellipse cx="20" cy="20" rx="7" ry="17"/><path d="M3 20h34M6 11h28M6 29h28"/></svg>
      <div><h4>Global Support</h4><p>But I must explain to you how all this mistaken idea of denouncing pleasure and praising pain was born and I will give you a complete account of the system.</p></div>
    </div>
    <div class="feature">
      <svg width="40" height="40" viewBox="0 0 40 40" fill="none" stroke="#1e8cf0" stroke-width="2"><circle cx="20" cy="20" r="17"/><circle cx="20" cy="20" r="10"/><circle cx="20" cy="20" r="3" fill="#1e8cf0"/></svg>
      <div><h4>Our Mission</h4><p>But I must explain to you how all this mistaken idea of denouncing pleasure and praising pain was born and I will give you a complete account of the system.</p></div>
    </div>
    <div class="feature">
      <svg width="40" height="40" viewBox="0 0 40 40" fill="#1e8cf0"><rect x="4" y="26" width="6" height="10"/><rect x="13" y="20" width="6" height="16"/><rect x="22" y="14" width="6" height="22"/><rect x="31" y="6" width="6" height="30"/></svg>
      <div><h4>100% Success Rate</h4><p>But I must explain to you how all this mistaken idea of denouncing pleasure and praising pain was born and I will give you a complete account of the system.</p></div>
    </div>
    <div class="feature">
      <svg width="40" height="40" viewBox="0 0 40 40" fill="none" stroke="#1e8cf0" stroke-width="2"><circle cx="20" cy="20" r="17"/><path d="M12 21l6 6 11-13"/></svg>
      <div><h4>Customer Satisfaction</h4><p>But I must explain to you how all this mistaken idea of denouncing pleasure and praising pain was born and I will give you a complete account of the system.</p></div>
    </div>
  </div>
</section>

<section class="resources">
  <h2 class="section-title">Resources</h2>
  <div class="tiles">
    <div class="tile" style="background:linear-gradient(135deg,#2b2f36,#6e747c)" role="img" aria-label="Hands typing on a laptop"><span>LOREM IPSUM DOLOR</span></div>
    <div class="tile" style="background:linear-gradient(135deg,#3e4450,#8a8f98)" role="img" aria-label="Team meeting around a table"><span>LOREM IPSUM DOLOR</span></div>
    <div class="tile" style="background:linear-gradient(135deg,#a9a6a0,#4f4c48)" role="img" aria-label="Colleagues in a bright office"><span>LOREM IPSUM DOLOR</span></div>
    <div class="tile" style="background:linear-gradient(135deg,#41474f,#9aa0a6)" role="img" aria-label="Man speaking to a small group"><span>LOREM IPSUM DOLOR</span></div>
    <div class="tile" style="background:linear-gradient(135deg,#5a6068,#c7c9cc)" role="img" aria-label="Presenter at a whiteboard"><span>LOREM IPSUM DOLOR</span></div>
    <div class="tile" style="background:linear-gradient(135deg,#4c5561,#b2b7bd)" role="img" aria-label="Workshop with an audience"><span>LOREM IPSUM DOLOR</span></div>
  </div>
</section>

<section class="blog">
  <h2 class="section-title">Latest Blog</h2>
  <div class="posts">
    <div class="post">
      <div class="photo" style="left:0;background:linear-gradient(180deg,#cfd2d6,#6a5e56)" role="img" aria-label="Man in sunglasses outdoors"></div>
      <div class="post-copy" style="left:150px">
        <h3>Sed ut perspiciatis unde omnis iste natus error sit</h3>
        <p>But I must explain to you how all this mistaken idea of denouncing pleasure and praising pain was born.</p>
        <span class="btn">Read More</span>
      </div>
    </div>
    <div class="post">
      <div class="post-copy" style="left:24px">
        <h3>But I must explain to you how all this mistaken idea</h3>
        <p>But I must explain to you how all this mistaken idea of denouncing pleasure and praising pain was born.</p>
        <span class="btn">Read More</span>
      </div>
      <div class="photo" style="right:0;background:linear-gradient(180deg,#e4e6e8,#8fa0b0)" role="img" aria-label="Smiling man in a shirt"></div>
    </div>
  </div>
  <div class="dots"><i class="on"></i><i></i><i></i><i></i></div>
</section>

<footer class="site-footer">
  <div class="foot-about">
    <p>But I must explain to you how all this mistaken idea of denouncing pleasure and praising pain was born and I will give you a complete account of the system.</p>
    <p>Nor again is there anyone who loves or pursues or desires to obtain pain of itself, because it is pain, but occasionally circumstances occur in which toil can procure great pleasure.</p>
  </div>
  <div class="follow">
    <h5>FOLLOW US</h5>
    <div class="socials"><i></i><i></i><i></i><i></i><i></i><i></i></div>
  </div>
  <div class="foot-nav">Home | About | Blog | Video | Resources | Contact</div>
  <div class="foot-rule"></div>
  <div class="copyright">Copyright &copy; 2019 All Rights Reserved</div>
</footer>

</body>
</html>
```